Pet label template for Vantoreli mexican based company

Hello, Vantoreli is a mexican based company dedicated to manufacture and sell its propietary brands for human health care. We are now introducing a new "Pet" category to our Brand. It´s name is Vantoreli Pets (logo attached).
We are lookoig for the design template for our package labels that will most probably be in plastic bags like the example attaches (Pet meadows of brookfield). It is important to point out that the labels are going to be pasted on the bags and not directly printed on the bags itself like the examples attached.

I am attaching some examples but please feel free to innovate your own desing. I am also attaching the logo that must be in every label.

Target Market(s)

Pet owners basically dogs and cats.

Industry/Entity Type

Health Care

Font styles to use
Other font styles liked:
• something easy to read

Requirements
Must have
• We like both simple elegant designs and bright colorful ones son feel free to innovate.
Nice to have
• Illustration of both cat or dog for their product label.

```html
<!DOCTYPE html>
<html lang="en">
<head>
<meta charset="utf-8">
<title>Vantoreli Pets – Immunity Label</title>
<link rel="stylesheet" href="https://fonts.googleapis.com/css2?family=Cinzel:wght@700&family=Quicksand:wght@700&family=Oswald:wght@600&family=Comfortaa:wght@700&display=swap">
<style>
  :root {
    --canvas-bg: #eceae6;
    --label-white: #ffffff;
    --label-shade: #e9eaea;
    --forest: #1f6b2e;
    --green: #2a9a3c;
    --lime: #7dc242;
    --olive-lime: #a6c23a;
    --teal: #35a272;
    --wave-dark: #135c1f;
    --wave-mid: #1f8a22;
    --wave-bright: #38b12c;
    --wave-light: #7cc242;
    --silhouette: #2b2b2b;
  }
  * { box-sizing: border-box; margin: 0; padding: 0; }
  html, body { width: 1200px; height: 1096px; overflow: hidden; background: var(--canvas-bg); }
  .label {
    position: relative;
    width: 1200px; height: 1096px;
    background: radial-gradient(ellipse at 60% 40%, var(--label-white) 0%, var(--label-shade) 100%);
    overflow: hidden;
  }
  .brand {
    position: absolute; top: 70px; left: 0; width: 100%;
    display: flex; flex-direction: column; align-items: center; gap: 18px;
  }
  .brand-dot { width: 74px; height: 74px; border-radius: 50%; background: var(--green); }
  .brand-name {
    font-family: "Cinzel", serif; font-weight: 700; font-size: 64px;
    color: var(--forest); letter-spacing: 3px;
  }
  .product-name {
    position: absolute; top: 268px; left: 0; width: 100%; text-align: center;
    font-family: "Quicksand", sans-serif; font-weight: 700; font-size: 176px;
    line-height: 1; color: var(--lime); letter-spacing: -2px;
  }
  .product-tagline {
    position: absolute; top: 458px; left: 0; width: 100%; text-align: center;
    font-family: "Oswald", sans-serif; font-weight: 600; font-size: 26px;
    color: var(--forest); letter-spacing: 1px;
  }
  .benefits { position: absolute; top: 540px; left: 110px; list-style: none; }
  .benefit {
    display: flex; align-items: center; gap: 12px;
    font-family: "Comfortaa", sans-serif; font-weight: 700; font-size: 24px;
    margin-bottom: 22px;
  }
  .benefit-text { padding-bottom: 4px; border-bottom: 3px dotted currentColor; }
  .benefit--immune { color: var(--green); }
  .benefit--cardio { color: var(--olive-lime); margin-left: 14px; }
  .benefit--liver { color: var(--teal); margin-left: 28px; }
  .grain-free {
    position: absolute; top: 700px; left: 130px;
    display: flex; flex-direction: column; align-items: flex-start; gap: 8px;
    font-family: "Oswald", sans-serif; font-weight: 600; font-size: 30px; color: var(--forest);
  }
  .pets-art {
    position: absolute; left: 600px; top: 500px; width: 430px; height: 330px;
    background: linear-gradient(180deg, #3a3a3a 0%, var(--silhouette) 100%);
    border-radius: 40px 120px 20px 20px; opacity: 0.9;
  }
  .waves { position: absolute; left: 0; top: 0; }
  .band-text { font-family: "Oswald", sans-serif; font-weight: 600; fill: #fff; }
</style>
</head>
<body>
<main class="label">
  <header class="brand">
    <span class="brand-dot"></span>
    <span class="brand-name">Vantoreli Pets</span>
  </header>

  <h1 class="product-name">Immunity</h1>
  <p class="product-tagline">IMMUNE SUPPORT FOR PETS</p>

  <ul class="benefits">
    <li class="benefit benefit--immune">
      <svg width="34" height="34" viewBox="0 0 34 34" fill="none" stroke="currentColor" stroke-width="2"><circle cx="17" cy="17" r="9"/><path d="M17 2v30M2 17h30" stroke-dasharray="3 3"/></svg>
      <span class="benefit-text">Support Immune System</span>
    </li>
    <li class="benefit benefit--cardio">
      <svg width="34" height="34" viewBox="0 0 34 34" fill="none" stroke="currentColor" stroke-width="2"><circle cx="17" cy="17" r="9"/><path d="M17 2v30M2 17h30" stroke-dasharray="3 3"/></svg>
      <span class="benefit-text">Cardiovascular System</span>
    </li>
    <li class="benefit benefit--liver">
      <svg width="34" height="34" viewBox="0 0 34 34" fill="none" stroke="currentColor" stroke-width="2"><circle cx="17" cy="17" r="9"/><path d="M17 2v30M2 17h30" stroke-dasharray="3 3"/></svg>
      <span class="benefit-text">Liver Function</span>
    </li>
  </ul>

  <div class="grain-free">
    <svg width="90" height="46" viewBox="0 0 90 46"><path d="M4 42 C10 10 40 4 46 4 C44 26 28 42 4 42Z" fill="#9fd64a"/><path d="M36 42 C46 16 80 10 88 12 C80 32 62 44 36 42Z" fill="#2f8f3a"/></svg>
    <span>GRAIN FREE</span>
  </div>

  <div class="pets-art" role="img" aria-label="Black silhouettes of a cat and a large dog sitting side by side"></div>

  <svg class="waves" width="1200" height="1096" viewBox="0 0 1200 1096">
    <path d="M0 770 C300 790 700 930 1200 800 L1200 1096 L0 1096Z" fill="var(--wave-light)"/>
    <path d="M0 820 C320 840 700 990 1200 840 L1200 1096 L0 1096Z" fill="var(--wave-mid)"/>
    <path d="M0 880 C360 860 760 1000 1200 880 L1200 1096 L0 1096Z" fill="var(--wave-dark)"/>
    <path d="M0 930 C300 900 800 1040 1200 920 L1200 1096 L0 1096Z" fill="var(--wave-bright)"/>
    <path d="M0 1000 C400 960 800 1080 1200 980 L1200 1096 L0 1096Z" fill="var(--wave-mid)"/>
    <path d="M0 1050 C400 1030 800 1090 1200 1040 L1200 1096 L0 1096Z" fill="var(--wave-dark)"/>
    <text class="band-text" font-size="26" transform="translate(170 818) rotate(9)">PROBIOTICS   VITAMINS   ANTIOXIDANTS</text>
    <text class="band-text" font-size="18" transform="translate(60 830) rotate(9)">NET WT 2.12 OZ. (60G)</text>
  </svg>
</main>
</body>
</html>
```